DESKHAVEN COSPACE Website design and coding

DESKHAVEN COSPACE

DESKHAVEN is Galveston’s first (and currently only) shared business co-working space. We share the same upscale, casual work environment, but we work independently on our own (or our team’s) projects and goals. For only a flat $195 membership fee per month, you have your very own all-inclusive, fun, personal business office environment. Website is written (Word file #12, below); and all pictures etc provided. Galveston is a beachy, coastal, historic city an hour from Houston, Texas USA. Logo (file 11 below) is temporary only.

Target Market(s)

Outside sales people, medical students looking for study hall, Houston companies looking for local office, real estate agents, graphic artists, entrepreneurs, etc

Contact Information for Business Card

will discuss --want to combine with current business card with multiple businesses

Logo Text

DESKHAVEN COSPACE

Coding

Coded - Design and coding required

Number of Pages Required

5+ page

Colors
ec1f27
fbed22

Requirements
Nice to have
• maroon/wine dominant with yellow and red accents, gray base are the colors of the space--website could coordinate--but open to creative ideas/combinations

```html
<!DOCTYPE html>
<html lang="en">
<head>
<meta charset="utf-8">
<title>Deskhaven Cospace – Contact</title>
<link rel="stylesheet" href="https://fonts.googleapis.com/css2?family=Catamaran:wght@400;500;600;700;800&display=swap">
<style>
:root{
  --maroon:#860000;
  --yellow:#f8d000;
  --ink:#1b1b1b;
  --base:#f3f3f3;
  --white:#ffffff;
  --line:#d6d6d6;
}
*{margin:0;padding:0;box-sizing:border-box}
html,body{width:740px;height:1200px;overflow:hidden}
body{font-family:"Catamaran",sans-serif;color:var(--ink);background:var(--base);position:relative}
.abs{position:absolute}
.site-header{left:0;top:0;width:740px;height:37px;background:var(--maroon)}
.brand{left:69px;top:11px;font-size:11.5px;font-weight:700;color:var(--yellow);letter-spacing:.2px;line-height:14px}
.nav a{position:absolute;top:13px;font-size:8.6px;font-weight:500;color:var(--white);text-decoration:none;line-height:10px}
.nav a.active{color:var(--yellow)}
.nav a.active::after{content:"";position:absolute;left:0;right:0;top:13px;height:1.5px;background:var(--yellow)}
.hero{left:0;top:37px;width:740px;height:201px;background:linear-gradient(100deg,#d9d9d9 0%,#bdbdbd 30%,#8a8a8a 60%,#5c5c5c 80%,#9a9a9a 100%)}
.hero-title{left:0;top:97px;width:740px;text-align:center;font-size:27px;font-weight:700;color:var(--white);line-height:32px}
.crumbs{left:0;top:150px;width:740px;text-align:center;font-size:8px;color:var(--white);line-height:10px}
.crumbs span.home{color:var(--yellow)}
.sec-title{font-size:18.5px;font-weight:700;color:var(--maroon);line-height:22px}
.sec-title span{font-weight:500}
.rule{height:2px;width:54px;background:var(--yellow)}
.details p{position:absolute;left:0;font-size:8.2px;line-height:10px;white-space:nowrap}
.details b{font-weight:700;margin-right:4px}
.details .ind{left:16px}
.form-card{left:327px;top:369px;width:344px;height:365px;background:var(--base);border-radius:5px;box-shadow:0 1px 5px rgba(0,0,0,.12)}
.field-label{font-size:7.4px;line-height:9px;color:var(--ink)}
.field{background:var(--white);border:1px solid var(--line);border-radius:4px;height:22px;width:138px}
.submit{left:354px;top:684px;width:68px;height:26px;border-radius:13px;background:var(--maroon);color:var(--white);font-size:8.4px;font-weight:700;text-align:center;line-height:26px}
.map{left:0;top:757px;width:740px;height:212px;background:linear-gradient(180deg,#efefef,#e6e6e6)}
.site-footer{left:0;top:969px;width:740px;height:231px;background:var(--maroon)}
.foot-state{left:33px;top:1030px;width:138px;height:100px;background:rgba(255,255,255,.05)}
.foot-brand{left:69px;top:1004px;font-size:13px;font-weight:700;color:var(--yellow);line-height:13.5px}
.foot-tag{left:69px;top:1050px;font-size:8.2px;color:var(--white);line-height:14.6px}
.foot-copy{left:69px;top:1111px;width:138px;text-align:center;font-size:5px;color:var(--white);line-height:11px}
.foot-copy .legal{color:var(--yellow)}
.foot-head{font-size:10.5px;font-weight:700;color:var(--yellow);line-height:12px}
.foot-list{font-size:8.2px;color:var(--white);line-height:14.6px;list-style:none}
.foot-list .hl{color:var(--yellow)}
</style>
</head>
<body>

<header class="site-header abs">
  <div class="brand abs">DESKHAVEN COSPACE</div>
  <nav class="nav">
    <a style="left:421px">Home</a>
    <a style="left:465px">About</a>
    <a style="left:510px">Amenities</a>
    <a style="left:572px">Membership</a>
    <a class="active" style="left:641px">Contact</a>
  </nav>
</header>

<section class="hero abs" role="img" aria-label="Photo of two professionals working in an office, one on a phone call"></section>
<h1 class="hero-title abs">Contact</h1>
<div class="crumbs abs"><span class="home">Home</span>&nbsp;&nbsp;→&nbsp;&nbsp;Contact</div>

<h2 class="sec-title abs" style="left:69px;top:299px">Contact <span>Details</span></h2>
<div class="rule abs" style="left:69px;top:336px"></div>

<div class="details abs" style="left:69px;top:371px">
  <p style="top:0"><b>Email:</b> hello@deskhavencospace.com</p>
  <p style="top:18.4px"><b>Phone:</b> 713-555-0148</p>
  <p style="top:36.8px"><b>Chatterbox:</b> https://www.chatterbox.net/DeskhavenCospace</p>
  <p style="top:55.2px"><b>Proflink:</b> https://www.proflink.net/in/deskhaven</p>
  <p style="top:73.6px"><b>Picturely:</b> https://www.picturely.net/deskhaven</p>
  <p style="top:92px"><b>Office location:</b></p>
  <p class="ind" style="top:110.4px">Deskhaven Cospace</p>
  <p class="ind" style="top:128.8px">418 Harbor Ave, Suite 101</p>
  <p class="ind" style="top:147.2px">Galveston, TX 77550</p>
  <p style="top:165.6px"><b>Owner:</b></p>
  <p class="ind" style="top:184px">Bellamy Holdings</p>
  <p class="ind" style="top:202.4px">reed@bellamyholdings.com</p>
  <p class="ind" style="top:220.8px">713-555-0148</p>
  <p style="top:239.2px"><b>Mailing address for management:</b></p>
  <p class="ind" style="top:257.6px">Bellamy Holdings</p>
  <p class="ind" style="top:276px">275 Market St., Suite 200</p>
  <p class="ind" style="top:294.4px">Houston, TX 77002</p>
</div>

<h2 class="sec-title abs" style="left:346px;top:302px">Contact <span>Form</span></h2>
<div class="rule abs" style="left:346px;top:339px"></div>

<div class="form-card abs"></div>
<div class="field-label abs" style="left:353px;top:397px">First Name</div>
<div class="field-label abs" style="left:510px;top:397px">Last Name</div>
<div class="field abs" style="left:354px;top:410px"></div>
<div class="field abs" style="left:503px;top:410px"></div>

<div class="field-label abs" style="left:354px;top:440px">Address</div>
<div class="field-label abs" style="left:510px;top:440px">City</div>
<div class="field abs" style="left:354px;top:453px"></div>
<div class="field abs" style="left:503px;top:453px"></div>

<div class="field-label abs" style="left:354px;top:483px">State</div>
<div class="field-label abs" style="left:510px;top:483px">Zip Code</div>
<div class="field abs" style="left:354px;top:497px"></div>
<div class="field abs" style="left:503px;top:497px"></div>

<div class="field-label abs" style="left:354px;top:526px">Email</div>
<div class="field-label abs" style="left:514px;top:526px">Phone</div>
<div class="field abs" style="left:354px;top:540px"></div>
<div class="field abs" style="left:503px;top:540px"></div>

<div class="field-label abs" style="left:354px;top:569px">Description Of Business</div>
<div class="field abs" style="left:354px;top:586px;width:291px"></div>

<div class="field-label abs" style="left:354px;top:612px">Your Message</div>
<div class="field abs" style="left:354px;top:628px;width:291px;height:40px"></div>

<div class="submit abs">Submit</div>

<section class="map abs" role="img" aria-label="Street map of downtown Galveston with a pin marking the Deskhaven Cospace office"></section>

<footer class="site-footer abs"></footer>
<div class="foot-state abs" role="img" aria-label="Faint dotted outline of the state of Texas"></div>
<div class="foot-brand abs">DESKHAVEN<br>COSPACE</div>
<p class="foot-tag abs">Galveston’s first &nbsp;shared business<br>co-working space</p>
<div class="foot-copy abs">©2020 Deskhaven. All Rights Reserved.<br><span class="legal">Terms of Use | Privacy Policy</span></div>

<h3 class="foot-head abs" style="left:294px;top:1008px">Menu</h3>
<div class="rule abs" style="left:294px;top:1028px"></div>
<ul class="foot-list abs" style="left:291px;top:1047px">
  <li class="hl">Home</li><li>About</li><li>Amenities</li><li>Membership</li><li>Contact</li>
</ul>

<h3 class="foot-head abs" style="left:436px;top:1008px">Social</h3>
<div class="rule abs" style="left:436px;top:1028px"></div>
<ul class="foot-list abs" style="left:433px;top:1047px">
  <li>Chatterbox</li><li>Proflink</li><li>Picturely</li>
</ul>

<h3 class="foot-head abs" style="left:577px;top:1008px">Contact</h3>
<div class="rule abs" style="left:577px;top:1028px"></div>
<ul class="foot-list abs" style="left:574px;top:1047px">
  <li>418 Harbor Ave.</li><li>Ste. 101</li><li>Galveston, TX 77550</li><li>713-555-0148</li><li class="hl">reed@bellamyholdings.com</li>
</ul>

</body>
</html>
```